Brookmere Osteopathy flyer

I want a clean clear DL flyer (but also want an A4 poster) promoting a new Osteopathic business in a semi rural area in Tasmania (Australia).
It can have pictures like the examples attached to show people what Osteopathy is (its like Chiropractic and physiotherapy).
I am the sole practioner and am male, so any pictures would be best to be a white male if possible.
I've attached some wording, you can use all, or none of it
I don't have a phone number for the business yet
info@brookmereosteopathy.example
www.brookmereosteopathy.example
Target Market(s)
Australians, from tradies, professionals, babies to retired people
Industry/Entity Type
Health
Look and feel

```html
<!DOCTYPE html>
<html lang="en">
<head>
<meta charset="utf-8">
<title>Brookmere Osteopathy flyer</title>
<link rel="stylesheet" href="https://fonts.googleapis.com/css2?family=Lexend:wght@600&family=Montserrat:wght@500&family=Nunito:wght@800&family=Oswald:wght@700&display=swap">
<style>
  :root {
    --blue: #1a96d4;
    --blue-light: #6fcbeb;
    --ink: #111111;
    --paper: #ffffff;
    --panel-grey: #f1f1f3;
    --backdrop: #424242;
    --skin: #e7c2a6;
    --navy: #2b3a6b;
  }
  * { margin: 0; padding: 0; box-sizing: border-box; }
  html, body { width: 897px; height: 1200px; overflow: hidden; background: var(--backdrop); }
  .flyer {
    position: absolute; left: 16px; top: 0;
    width: 1272px; height: 1765px;
    transform: scale(0.68); transform-origin: top left;
    background: var(--paper); overflow: hidden;
  }
  .hero-art { position: absolute; left: 0; top: 0; width: 1272px; height: 1120px; }
  .brand-title {
    position: absolute; left: 72px; top: 52px;
    font-family: "Lexend", sans-serif; font-weight: 600;
    font-size: 100px; line-height: 86px; letter-spacing: 0.01em;
  }
  .brand-title .line-1 { color: var(--blue); display: block; }
  .brand-title .line-2 { color: var(--blue-light); display: block; }
  .tagline {
    position: absolute; left: 78px; top: 232px;
    font-family: "Oswald", sans-serif; font-weight: 700;
    font-size: 60px; color: var(--ink); letter-spacing: 0.005em;
  }
  .brand-badge {
    position: absolute; left: 795px; top: 43px; width: 280px; height: 280px;
    border-radius: 50%; background: var(--paper); border: 3px solid var(--blue-light);
    display: flex; align-items: center; justify-content: center; text-align: center;
    font-family: "Montserrat", sans-serif; font-weight: 500; font-size: 30px; line-height: 38px;
    color: var(--blue);
  }
  .reasons { position: absolute; left: 88px; top: 1140px; }
  .reasons-heading { font-family: "Nunito", sans-serif; font-weight: 800; letter-spacing: -0.02em; }
  .reasons-heading .lead { display: block; color: var(--blue-light); font-size: 48px; line-height: 60px; }
  .reasons-heading .main { display: block; color: var(--blue); font-size: 52px; line-height: 60px; }
  .reasons-list { list-style: none; margin-top: 24px; font-family: "Montserrat", sans-serif; font-weight: 500; font-size: 28px; color: var(--ink); }
  .reasons-list li { display: flex; align-items: center; height: 39px; }
  .reasons-list svg { width: 24px; height: 24px; margin-right: 14px; flex: none; }
  .side-panel { position: absolute; left: 775px; top: 1093px; width: 427px; height: 672px; background: var(--panel-grey); }
  .about-box {
    position: absolute; left: 775px; top: 1093px; width: 427px; height: 460px;
    background: var(--blue); border-radius: 14px 14px 22px 22px;
    padding: 56px 26px 0; color: var(--paper); text-align: center;
    font-family: "Montserrat", sans-serif; font-weight: 500; font-size: 19.5px; line-height: 27px;
  }
  .contact { position: absolute; left: 798px; top: 1592px; list-style: none; font-family: "Montserrat", sans-serif; font-weight: 500; font-size: 21px; color: var(--ink); }
  .contact li { display: flex; align-items: center; height: 27px; }
  .contact svg { width: 18px; height: 18px; margin-right: 10px; flex: none; }
</style>
</head>
<body>
<main class="flyer">
  <svg class="hero-art" viewBox="0 0 1272 1120" xmlns="http://www.w3.org/2000/svg">
    <defs>
      <linearGradient id="treatmentTones" x1="0" y1="0" x2="1" y2="1">
        <stop offset="0" stop-color="#2b3a6b"/>
        <stop offset="0.45" stop-color="#d9b295"/>
        <stop offset="0.8" stop-color="#e8c6ab"/>
        <stop offset="1" stop-color="#f2f2f2"/>
      </linearGradient>
      <linearGradient id="skinTones" x1="0" y1="0" x2="1" y2="1">
        <stop offset="0" stop-color="#f3ece6"/>
        <stop offset="1" stop-color="#d7aa8c"/>
      </linearGradient>
    </defs>
    <path class="wave-band" fill="#1a96d4" d="M920 0 L950 0 C915 260 790 405 560 412 C320 420 205 440 225 570 C255 760 430 905 610 1015 L560 1045 C300 900 58 720 58 560 C56 420 300 396 520 392 C760 388 885 250 920 0 Z"/>
    <path role="img" aria-label="Photo: osteopath's hands treating a patient's lower back on a treatment table" fill="url(#treatmentTones)" d="M950 0 L1272 0 L1272 1095 C1100 1108 900 1100 700 1060 C500 1000 300 800 245 600 C215 480 330 432 560 422 C780 412 925 250 950 0 Z"/>
    <circle cx="235" cy="828" r="187" fill="#ffffff"/>
    <circle role="img" aria-label="Photo: practitioner working on a patient's shoulder" cx="235" cy="828" r="175" fill="url(#skinTones)"/>
    <circle cx="600" cy="968" r="157" fill="#ffffff"/>
    <circle role="img" aria-label="Photo: hands supporting a patient's neck and shoulder" cx="600" cy="968" r="145" fill="url(#skinTones)"/>
  </svg>

  <h1 class="brand-title"><span class="line-1">BROOKMERE</span><span class="line-2">OSTEOPATHY</span></h1>
  <p class="tagline">Move better, feel better.</p>
  <div class="brand-badge">Brookmere<br>Osteopathy</div>

  <section class="reasons">
    <h2 class="reasons-heading"><span class="lead">Common Reasons</span><span class="main">People Visit An Osteopath:</span></h2>
    <ul class="reasons-list">
      <li><svg viewBox="0 0 24 24"><circle cx="12" cy="12" r="10" fill="none" stroke="#1a96d4" stroke-width="2"/><path d="M7 12 l4 4 l9 -10" fill="none" stroke="#1a96d4" stroke-width="2.6" stroke-linecap="round" stroke-linejoin="round"/></svg>Back / neck pain</li>
      <li><svg viewBox="0 0 24 24"><circle cx="12" cy="12" r="10" fill="none" stroke="#1a96d4" stroke-width="2"/><path d="M7 12 l4 4 l9 -10" fill="none" stroke="#1a96d4" stroke-width="2.6" stroke-linecap="round" stroke-linejoin="round"/></svg>Headaches / migraines</li>
      <li><svg viewBox="0 0 24 24"><circle cx="12" cy="12" r="10" fill="none" stroke="#1a96d4" stroke-width="2"/><path d="M7 12 l4 4 l9 -10" fill="none" stroke="#1a96d4" stroke-width="2.6" stroke-linecap="round" stroke-linejoin="round"/></svg>Joint and muscle pain</li>
      <li><svg viewBox="0 0 24 24"><circle cx="12" cy="12" r="10" fill="none" stroke="#1a96d4" stroke-width="2"/><path d="M7 12 l4 4 l9 -10" fill="none" stroke="#1a96d4" stroke-width="2.6" stroke-linecap="round" stroke-linejoin="round"/></svg>Pregnancy-related discomfort</li>
      <li><svg viewBox="0 0 24 24"><circle cx="12" cy="12" r="10" fill="none" stroke="#1a96d4" stroke-width="2"/><path d="M7 12 l4 4 l9 -10" fill="none" stroke="#1a96d4" stroke-width="2.6" stroke-linecap="round" stroke-linejoin="round"/></svg>Disc related issues</li>
      <li><svg viewBox="0 0 24 24"><circle cx="12" cy="12" r="10" fill="none" stroke="#1a96d4" stroke-width="2"/><path d="M7 12 l4 4 l9 -10" fill="none" stroke="#1a96d4" stroke-width="2.6" stroke-linecap="round" stroke-linejoin="round"/></svg>Sciatica</li>
      <li><svg viewBox="0 0 24 24"><circle cx="12" cy="12" r="10" fill="none" stroke="#1a96d4" stroke-width="2"/><path d="M7 12 l4 4 l9 -10" fill="none" stroke="#1a96d4" stroke-width="2.6" stroke-linecap="round" stroke-linejoin="round"/></svg>Plantar fasciitis</li>
      <li><svg viewBox="0 0 24 24"><circle cx="12" cy="12" r="10" fill="none" stroke="#1a96d4" stroke-width="2"/><path d="M7 12 l4 4 l9 -10" fill="none" stroke="#1a96d4" stroke-width="2.6" stroke-linecap="round" stroke-linejoin="round"/></svg>Tendonitis / Bursitis</li>
      <li><svg viewBox="0 0 24 24"><circle cx="12" cy="12" r="10" fill="none" stroke="#1a96d4" stroke-width="2"/><path d="M7 12 l4 4 l9 -10" fill="none" stroke="#1a96d4" stroke-width="2.6" stroke-linecap="round" stroke-linejoin="round"/></svg>Adhesive capsulitis (frozen shoulder)</li>
      <li><svg viewBox="0 0 24 24"><circle cx="12" cy="12" r="10" fill="none" stroke="#1a96d4" stroke-width="2"/><path d="M7 12 l4 4 l9 -10" fill="none" stroke="#1a96d4" stroke-width="2.6" stroke-linecap="round" stroke-linejoin="round"/></svg>Tennis / Golfers elbow</li>
    </ul>
  </section>

  <div class="side-panel"></div>
  <p class="about-box">Brookmere Osteopathy use a tailored combination of joint mobilisation/manipulation, stretching, movement, trigger point dry needling and targeted massage to reduce pain and restore optimal function. Hands-on treatment is backed up with rehabilitative exercise prescription and advice. So whether you're recovering from injury or managing chronic discomfort, we’re here to help you move better and feel your best.</p>

  <ul class="contact">
    <li><svg viewBox="0 0 24 24"><path d="M12 22 C12 22 5 14 5 9 a7 7 0 0 1 14 0 C19 14 12 22 12 22 Z" fill="none" stroke="#1a96d4" stroke-width="1.8"/><circle cx="12" cy="9" r="2.5" fill="none" stroke="#1a96d4" stroke-width="1.8"/></svg>48 Wattle Creek road, Brookmere</li>
    <li><svg viewBox="0 0 24 24"><circle cx="12" cy="12" r="9.5" fill="none" stroke="#1a96d4" stroke-width="1.8"/><ellipse cx="12" cy="12" rx="4" ry="9.5" fill="none" stroke="#1a96d4" stroke-width="1.6"/><path d="M2.5 12 H21.5" stroke="#1a96d4" stroke-width="1.6"/></svg>www.brookmereosteopathy.example</li>
    <li><svg viewBox="0 0 24 24"><rect x="2.5" y="5" width="19" height="14" rx="1.5" fill="none" stroke="#1a96d4" stroke-width="1.8"/><path d="M3 6 L12 13 L21 6" fill="none" stroke="#1a96d4" stroke-width="1.8"/></svg>info@brookmereosteopathy.example</li>
  </ul>
</main>
</body>
</html>
```